Modern Business Card

Modern professional business card with more than just logo and demographic info. Something memorable.

We are a trendy/modern chiropractic group with an emphasis on neurology, hence the minimalist-type brain logo. We want to convey that modern and technical aspect with professionalism and the elite nature of our practice environment.

```html
<!DOCTYPE html>
<html lang="en">
<head>
<meta charset="utf-8">
<title>Meridian Spine Business Card</title>
<link href="https://fonts.googleapis.com/css2?family=Crimson+Text:wght@400&family=Ubuntu:wght@400;500&display=swap" rel="stylesheet">
<style>
  :root {
    --backdrop: #e8e5e0;
    --card-light: #ffffff;
    --card-dark: #0b0f14;
    --brand-blue: #5a80b6;
    --ink: #2a2a2a;
    --ink-soft: #444;
    --ink-muted: #6c6f74;
    --rule: #333;
  }
  * { margin: 0; padding: 0; box-sizing: border-box; }
  html, body { width: 1200px; height: 859px; overflow: hidden; background: var(--backdrop); }
  .canvas { position: relative; width: 1200px; height: 859px; }
  .card {
    position: absolute; top: 289px; width: 500px; height: 284px; overflow: hidden;
    box-shadow: 0 6px 18px rgba(0,0,0,0.18);
  }
  .card-front { left: 60px; background: var(--card-light); }
  .card-back { left: 640px; background: radial-gradient(ellipse at 55% 45%, #131b26 0%, var(--card-dark) 70%); }

  .wordmark { font-family: "Crimson Text", serif; font-weight: 400; color: var(--ink); line-height: 1; }
  .wordmark .primary { display: block; font-size: 31px; letter-spacing: 0.5px; }
  .wordmark .secondary { display: block; font-size: 16.5px; letter-spacing: 3px; margin-top: -1px; }
  .card-front .wordmark { position: absolute; left: 27px; top: 33px; }

  .person { position: absolute; left: 27px; top: 124px; }
  .person-name { font-family: "Crimson Text", serif; font-size: 20px; color: var(--ink-soft); letter-spacing: 0.3px; line-height: 1; }
  .person-role { font-family: "Ubuntu", sans-serif; font-size: 12.5px; color: var(--brand-blue); margin-top: 3px; }
  .divider { position: absolute; left: 27px; top: 180px; width: 150px; height: 1.5px; background: var(--rule); }

  .contact { position: absolute; left: 27px; top: 197px; list-style: none; font-family: "Ubuntu", sans-serif; font-size: 12.5px; color: var(--ink); }
  .contact li { display: flex; align-items: center; height: 17.5px; }
  .contact svg { width: 13px; height: 13px; margin-right: 6px; flex: none; }
  .contact .accent { color: var(--brand-blue); }

  .accent-block { position: absolute; background: var(--brand-blue); }
  .card-front .accent-block { left: 305px; top: 0; width: 195px; height: 284px; border-radius: 30px 0 0 30px; }
  .card-back .accent-block { left: -40px; top: 30px; width: 110px; height: 224px; border-radius: 0 30px 30px 0; }

  .back-lockup { position: absolute; left: 128px; top: 112px; display: flex; align-items: center; }
  .back-lockup .mark { width: 44px; height: 44px; border-radius: 50%; background: var(--brand-blue); margin-right: 14px; }
  .back-lockup .wordmark { color: #f3f3f3; }
  .back-lockup .wordmark .primary { font-size: 38px; }
  .back-lockup .wordmark .secondary { font-size: 19px; color: var(--ink-muted); letter-spacing: 4px; }
</style>
</head>
<body>
<div class="canvas">
  <section class="card card-front">
    <div class="wordmark">
      <span class="primary">MERIDIAN</span>
      <span class="secondary">SPINE</span>
    </div>
    <div class="accent-block" aria-hidden="true"></div>

    <div class="person">
      <p class="person-name">LENA MARSH</p>
      <p class="person-role">Training Specialist</p>
    </div>
    <div class="divider"></div>

    <ul class="contact">
      <li>
        <svg viewBox="0 0 16 16" fill="none" stroke="#2f5f9e" stroke-width="1.4"><circle cx="8" cy="8" r="6.6"/><path d="M5.5 4.8c.4-.4.9-.3 1.1.1l.6 1.2c.1.3 0 .6-.2.8l-.4.3c.4.9 1.1 1.6 2 2l.3-.4c.2-.2.5-.3.8-.2l1.2.6c.4.2.5.7.1 1.1-.6.6-1.4.8-2.2.4-1.7-.8-2.9-2-3.7-3.7-.4-.8-.2-1.6.4-2.2z"/></svg>
        555.201.4478
      </li>
      <li>
        <svg viewBox="0 0 16 16" fill="none" stroke="#2f5f9e" stroke-width="1.4"><rect x="1.5" y="3.5" width="13" height="9" rx="1"/><path d="M1.8 4l6.2 5 6.2-5"/></svg>
        l.marsh@meridianspine.com
      </li>
      <li>
        <svg viewBox="0 0 16 16" fill="none" stroke="#2f5f9e" stroke-width="1.3"><circle cx="8" cy="8" r="6.5"/><ellipse cx="8" cy="8" rx="2.8" ry="6.5"/><path d="M1.5 8h13M2.5 4.8h11M2.5 11.2h11"/></svg>
        <span>www.<span class="accent">meridianspine</span>.com</span>
      </li>
    </ul>
  </section>

  <section class="card card-back">
    <div class="accent-block" aria-hidden="true"></div>
    <div class="back-lockup">
      <div class="mark"></div>
      <div class="wordmark">
        <span class="primary">MERIDIAN</span>
        <span class="secondary">SPINE</span>
      </div>
    </div>
  </section>
</div>
</body>
</html>
```